Blue Heron Journeys

We are a predominantly online travel agency with high-end (first/business class) clients. I'm looking to either have our existing logo revamped or a new logo created with business card layout. I prefer to work with existing logo if possible so it remains familiar with existing clientele. I have uploaded a yellow business card layout showing icons on one side of the card. I would like to keep my existing colours, not yellow. could the company name/tag line go over the icons?
Industry/Entity Type
Business
Contact Information for Business Card
Lucinda Fairley
Director
(I.A.T.A. 07715463)
(Corvano Pty. Ltd) ABN 61 574 203 918
512/18 Kendrick Lane
Wattle Reach | NSW 2577 | Australia
www.blueheronjourneys.com.au
m: + 61 (0) 417 588 130
t: + 61 (0) 2 9416 2058
e: lucinda@blueheronjourneys.com.au

```html
<!DOCTYPE html>
<html lang="en">
<head>
<meta charset="utf-8">
<title>Blue Heron Journeys — Business Card</title>
<link rel="stylesheet" href="https://fonts.googleapis.com/css2?family=Lato:wght@400;700&family=Questrial&display=swap">
<style>
  :root {
    --backdrop: #777372;
    --card-light: #ffffff;
    --card-dark: #000000;
    --ink: #111111;
    --ink-soft: #333333;
    --rule-light: #b9b9b9;
    --rule-dark: #8a8a8a;
    --paper-text: #ffffff;
  }
  * { margin: 0; padding: 0; box-sizing: border-box; }
  html, body { width: 1200px; height: 900px; overflow: hidden; }
  body { background: var(--backdrop); position: relative; font-family: "Lato", sans-serif; }

  .card {
    position: absolute;
    top: 307px;
    width: 438px;
    height: 270px;
    border-radius: 12px;
  }
  .card--front { left: 150px; background: var(--card-light); color: var(--ink); }
  .card--back  { left: 609px; background: var(--card-dark); color: var(--paper-text); }

  /* Front: vertical brand block */
  .brand-vertical {
    position: absolute;
    left: 82px;
    top: 136px;
    transform: translate(-50%, -50%) rotate(-90deg);
    white-space: nowrap;
    font-size: 21px;
    font-weight: 400;
    letter-spacing: 0.2px;
    color: var(--ink);
  }
  .brand-rule-vertical {
    position: absolute;
    left: 107px;
    top: 58px;
    width: 1px;
    height: 152px;
    background: var(--rule-light);
  }
  .tagline-vertical {
    position: absolute;
    left: 117px;
    top: 133px;
    transform: translate(-50%, -50%) rotate(-90deg);
    white-space: nowrap;
    font-family: "Questrial", sans-serif;
    font-size: 12px;
    letter-spacing: 0.8px;
    color: var(--ink-soft);
  }
  .divider {
    position: absolute;
    left: 168px;
    top: 55px;
    width: 2px;
    height: 159px;
    background: var(--rule-light);
  }

  /* Front: contact details */
  .contact {
    position: absolute;
    left: 188px;
    top: 60px;
  }
  .contact__name { font-size: 17px; font-weight: 700; line-height: 20px; letter-spacing: 0.2px; }
  .contact__role { font-size: 13px; line-height: 18px; margin-bottom: 5px; }
  .contact__address { font-size: 12.5px; line-height: 16px; margin-bottom: 7px; }
  .contact__list { list-style: none; font-size: 12.5px; line-height: 17px; }
  .contact__list li { display: flex; align-items: center; gap: 5px; }
  .contact__icon { width: 12px; height: 12px; flex: none; }

  /* Back: centred brand */
  .brand-centre {
    position: absolute;
    left: 0;
    right: 0;
    top: 96px;
    text-align: center;
    font-size: 34px;
    font-weight: 400;
    letter-spacing: 0.3px;
  }
  .brand-rule {
    position: absolute;
    left: 94px;
    top: 152px;
    width: 252px;
    height: 1px;
    background: var(--rule-dark);
  }
  .tagline {
    position: absolute;
    left: 0;
    right: 0;
    top: 159px;
    text-align: center;
    font-family: "Questrial", sans-serif;
    font-size: 16px;
    letter-spacing: 1.3px;
  }
</style>
</head>
<body>

<section class="card card--front" aria-label="Business card front">
  <div class="brand-vertical">Blue Heron Journeys</div>
  <div class="brand-rule-vertical"></div>
  <div class="tagline-vertical">journey in style</div>
  <div class="divider"></div>

  <div class="contact">
    <p class="contact__name">LORUM SMITH</p>
    <p class="contact__role">Managing Director</p>
    <p class="contact__address">421, Address line here,<br>Dummy Code, 45452<br>Country Name</p>
    <ul class="contact__list">
      <li>
        <svg class="contact__icon" viewBox="0 0 12 12" aria-hidden="true">
          <rect width="12" height="12" rx="2.5" fill="#111"/>
          <rect x="4" y="2.5" width="4" height="7" rx="0.8" fill="none" stroke="#fff" stroke-width="1"/>
        </svg>
        888 444 0000
      </li>
      <li>
        <svg class="contact__icon" viewBox="0 0 12 12" aria-hidden="true">
          <rect width="12" height="12" rx="2.5" fill="#111"/>
          <rect x="2.5" y="3.5" width="7" height="5" fill="none" stroke="#fff" stroke-width="0.9"/>
          <path d="M2.5 3.5 L6 6.3 L9.5 3.5" fill="none" stroke="#fff" stroke-width="0.9"/>
        </svg>
        info@webname.com
      </li>
      <li>
        <svg class="contact__icon" viewBox="0 0 12 12" aria-hidden="true">
          <rect width="12" height="12" rx="2.5" fill="#111"/>
          <circle cx="6" cy="6" r="3.3" fill="none" stroke="#fff" stroke-width="0.9"/>
          <path d="M2.7 6 H9.3 M6 2.7 C4.4 4.5 4.4 7.5 6 9.3 M6 2.7 C7.6 4.5 7.6 7.5 6 9.3" fill="none" stroke="#fff" stroke-width="0.7"/>
        </svg>
        www.webaddress.com
      </li>
    </ul>
  </div>
</section>

<section class="card card--back" aria-label="Business card back">
  <div class="brand-centre">Blue Heron Journeys</div>
  <div class="brand-rule"></div>
  <div class="tagline">journey in style</div>
</section>

</body>
</html>
```